Core Values Banner For Hearthwell Guards Inc

We want to take the core values for our small growing chimney service company and post them for our entire team to see on a daily basis. We want to be remind everyone how important this is too us all. IntegrityWe try to be honest and accountable in all aspects of our business, as well as in our personal interactions. We do what we say we will do, when we say we will do it, and how we say we will do it.Kaizen“Change for the best”We strive to constantly grow and improve, both personally and professionally. We own up to our mistakes and strive to resolve and learn from them. We actively seek feedback from our clients and each other. We believe the most innovative ideas come when we intentionally look for them.FamilyWe are a family-owned business, and we consider everyone who works here and every one we serve to be part of the family. Being honest and genuine with each other and our customers is what sets us apart. We put ourselves in our customer’s shoes and make recommendations as if it were our chimney, our home and our family.

Font styles to use
Serif
Sans Serif

Colors
ec1f27

Requirements
Must have
• This banner will be approximately 2.5' in height and 6 to 6.5' in width.
• I would like all 3 core values and there definitions listed on the banner
• check out the feel of our marketing on our website www.hearthwellguardsnx.com

```html
<!DOCTYPE html>
<html lang="en">
<head>
<meta charset="utf-8">
<title>Hearthwell Guards Inc – Core Values Banner</title>
<link rel="stylesheet" href="https://fonts.googleapis.com/css2?family=Lato:wght@400;700;900&display=swap">
<style>
  :root {
    --crimson: #c91f3a;
    --rose: #d02458;
    --white: #ffffff;
    --ghost: rgba(255, 255, 255, 0.09);
    --backdrop: #f2f2f2;
  }
  * { margin: 0; padding: 0; box-sizing: border-box; }
  html, body {
    width: 1200px;
    height: 534px;
    overflow: hidden;
    background: var(--backdrop);
  }
  .banner {
    display: flex;
    width: 1200px;
    height: 534px;
    font-family: "Lato", Arial, sans-serif;
    color: var(--white);
  }
  .value {
    position: relative;
    width: 400px;
    height: 534px;
    overflow: hidden;
    background: var(--crimson);
  }
  .value--kaizen { background: var(--rose); }
  .value__ghost {
    position: absolute;
    top: 34px;
    left: 0;
    width: 100%;
    text-align: center;
    font-weight: 900;
    font-size: 80px;
    line-height: 1;
    letter-spacing: 1px;
    color: var(--ghost);
    white-space: nowrap;
    z-index: 0;
  }
  .value__frame {
    position: absolute;
    top: 46px;
    left: 35px;
    width: 330px;
    height: 442px;
    z-index: 1;
  }
  .value__title {
    position: absolute;
    left: 0;
    width: 100%;
    top: 112px;
    text-align: center;
    font-weight: 700;
    font-size: 54px;
    line-height: 1;
    z-index: 2;
  }
  .value--kaizen .value__title { top: 98px; }
  .value__tagline {
    position: absolute;
    left: 0;
    width: 100%;
    top: 164px;
    text-align: center;
    font-weight: 700;
    font-size: 24px;
    line-height: 1;
    z-index: 2;
  }
  .value__text {
    position: absolute;
    left: 58px;
    width: 284px;
    top: 230px;
    font-size: 15px;
    line-height: 23.5px;
    text-align: justify;
    text-align-last: center;
    hyphens: manual;
    z-index: 2;
  }
  .value--integrity .value__text {
    top: 264px;
    text-align: center;
  }
</style>
</head>
<body>
  <main class="banner" aria-label="Hearthwell Guards Inc core values">

    <section class="value value--integrity">
      <span class="value__ghost" aria-hidden="true">Integrity</span>
      <svg class="value__frame" viewBox="0 0 330 442" aria-hidden="true">
        <g fill="none" stroke="#ffffff" stroke-width="13">
          <polyline points="160,6.5 6.5,6.5 6.5,435.5 126,435.5"/>
          <polyline points="172,6.5 323.5,6.5 323.5,435.5 204,435.5"/>
        </g>
        <rect x="147" y="417" width="36" height="36" fill="#ffffff"/>
      </svg>
      <h2 class="value__title">Integrity</h2>
      <p class="value__text">We try to be honest and accountable in all aspects of our business, as well as in our personal interactions. We do what we say we will do, when we say we will do it, and how we say we will do it.</p>
    </section>

    <section class="value value--kaizen">
      <span class="value__ghost" aria-hidden="true">Kaizen</span>
      <svg class="value__frame" viewBox="0 0 330 442" aria-hidden="true">
        <g fill="none" stroke="#ffffff" stroke-width="13">
          <polyline points="160,6.5 6.5,6.5 6.5,435.5 126,435.5"/>
          <polyline points="172,6.5 323.5,6.5 323.5,435.5 204,435.5"/>
        </g>
        <rect x="147" y="417" width="36" height="36" fill="#ffffff"/>
      </svg>
      <h2 class="value__title">Kaizen</h2>
      <p class="value__tagline">“Change for the best”</p>
      <p class="value__text">We strive to constantly grow and im&shy;prove, both personally and professionally. We own up to our mistakes and strive to resolve and learn from them. We actively seek feedback from our clients and each other. We believe the most innovative ideas come when we intentionally look for them.</p>
    </section>

    <section class="value value--family">
      <span class="value__ghost" aria-hidden="true">Family</span>
      <svg class="value__frame" viewBox="0 0 330 442" aria-hidden="true">
        <g fill="none" stroke="#ffffff" stroke-width="13">
          <polyline points="160,6.5 6.5,6.5 6.5,435.5 126,435.5"/>
          <polyline points="172,6.5 323.5,6.5 323.5,435.5 204,435.5"/>
        </g>
        <rect x="147" y="417" width="36" height="36" fill="#ffffff"/>
      </svg>
      <h2 class="value__title">Family</h2>
      <p class="value__text">We are a family-owned business, and we consider everyone who works here and every one we serve to be part of the family. Being honest and genuine with each other and our customers is what sets us apart. We put ourselves in our customer’s shoes and make recommendations as if it were our chimney, our home and our family.</p>
    </section>

  </main>
</body>
</html>
```